AGP letterhead

We need a letterhead design for our new company based in Los Angeles called "Amber Gate Pictures". We develop film and television projects. We work with investors, financiers, film production companies, film distribution and sales companies as well as studios. We would like to incorporate our logo (see attached) but make the letterhead simple and elegant. We need to include: logo, company address, phone number and company website.
Updates

Hello designers, Thanks for your submissions. For our letterhead, we are looking for something more simple and elegant. No heavy bars or lines. Make it feel light and clean. Not a lot of ink on the page. Use the logo and contact info but think "clean", "streamlined" and mostly white paper. Looking forward to seeing more... thanks! Amber Gate Pictures team

Target Market(s)

Studio executives, talent agents and agencies, financiers, investors.

Industry/Entity Type

It Company

Requirements
Must have
• Amber Gate Pictures logo (see attached). Logo may be cropped and altered appropriately for elegant letterhead design.
• Please include:
• COMPANY ADDRESS:
• Tolvane Arts Park
• 2850 Delmore Street
• Crest Hall, 2nd Floor
• Harbor Point, CA 90421
• COMPANY WEBSITE:
• www.ambergatepicturesco.example
• COMPANY PHONE NUMBER:
• 555-604-2187

```html
<!DOCTYPE html>
<html lang="en">
<head>
<meta charset="utf-8">
<title>Amber Gate Pictures – Letterhead</title>
<link href="https://fonts.googleapis.com/css2?family=Montserrat:wght@500;600&display=swap" rel="stylesheet">
<style>
  :root {
    --backdrop: #e6e8e9;
    --paper: #ffffff;
    --ink: #1c2126;
    --ink-soft: #5b6470;
    --rule: #8a9098;
    --accent: #2a9fd6;
    --watermark: #f3f4f5;
  }
  * { margin: 0; padding: 0; box-sizing: border-box; }
  html, body { width: 1200px; height: 1000px; overflow: hidden; }
  body {
    background: var(--backdrop);
    font-family: "Montserrat", Arial, sans-serif;
    position: relative;
  }
  .sheet {
    position: absolute;
    top: 215px;
    width: 392px;
    height: 563px;
    background: var(--paper);
  }
  .sheet--watermarked { left: 170px; }
  .sheet--plain { left: 610px; width: 398px; }

  .brand {
    position: absolute;
    display: flex;
    align-items: center;
    gap: 6px;
  }
  .sheet--watermarked .brand { left: 52px; top: 52px; }
  .sheet--plain .brand { left: 53px; top: 50px; }
  .brand__dot {
    width: 18px; height: 18px;
    border-radius: 50%;
    background: var(--accent);
    flex: none;
  }
  .brand__square {
    width: 18px; height: 18px;
    background: var(--ink);
    flex: none;
  }
  .brand__name {
    font-weight: 600;
    font-size: 11px;
    letter-spacing: 0.06em;
    text-transform: uppercase;
    color: var(--ink);
    line-height: 1.1;
    width: 80px;
  }

  .watermark {
    position: absolute;
    left: 66px;
    top: 208px;
    width: 270px;
    height: 290px;
  }

  .footer {
    position: absolute;
    left: 0;
    top: 533px;
    width: 208px;
  }
  .footer__rule {
    height: 1px;
    background: var(--rule);
    width: 100%;
  }
  .footer__details {
    display: flex;
    gap: 20px;
    padding: 5px 0 0 27px;
    font-weight: 500;
    font-size: 3.6px;
    line-height: 1.7;
    color: var(--ink-soft);
    white-space: nowrap;
  }
  .footer__address { font-style: normal; }
</style>
</head>
<body>

  <section class="sheet sheet--watermarked" aria-label="Letterhead with watermark">
    <div class="brand">
      <span class="brand__dot"></span>
      <span class="brand__name">Amber Gate Pictures</span>
    </div>
    <svg class="watermark" viewBox="0 0 270 290" aria-hidden="true">
      <circle cx="135" cy="145" r="132" fill="var(--watermark)"/>
    </svg>
    <footer class="footer">
      <div class="footer__rule"></div>
      <div class="footer__details">
        <address class="footer__address">
          Office: Tolvane Arts Park, 2850 Delmore Street, Crest Hall,<br>
          2nd Floor, Harbor Point, CA 90421
        </address>
        <div class="footer__contact">
          Tel: 555-604-2187<br>
          Web: www.ambergatepicturesco.example
        </div>
      </div>
    </footer>
  </section>

  <section class="sheet sheet--plain" aria-label="Plain letterhead">
    <div class="brand">
      <span class="brand__square"></span>
      <span class="brand__name">Amber Gate Pictures</span>
    </div>
    <footer class="footer">
      <div class="footer__rule"></div>
      <div class="footer__details">
        <address class="footer__address">
          Office: Tolvane Arts Park, 2850 Delmore Street, Crest Hall,<br>
          2nd Floor, Harbor Point, CA 90421
        </address>
        <div class="footer__contact">
          Tel: 555-604-2187<br>
          Web: www.ambergatepicturesco.example
        </div>
      </div>
    </footer>
  </section>

</body>
</html>
```